BUSINESS CARD - HALLORAN FIELD SERVICES

I would like to create a business card for my fertilizer spreading business. I would like to incorporate my existing logo and also a description of the services offered. The business card will be given to farmers so must be kept simple but effective. It will also be left in stores so much also be eye catching in order to stand out from other cards.

Target Market(s)

FARMERS

Requirements
Must have
• FRONT OF CARD = EXISTING LOGO + "CUSTOMISED SPREADING" below the logo

REAR Of CARD = SERVICES OFFERED AND CONTACT DETAILS

- Bulk fertilizer including Lime, Gypsum, Manure & Compost
- Granular fertilizer including Single Super, Urea, Gran-am, & Custom Blends
- Modern equipment - Autosteer & Variable Rate Capable
- Friendly & Reliable Service
- Contact Gus: 0417 552 308
Nice to have
• utilize same color scheme as existing logo

```html
<!DOCTYPE html>
<html lang="en">
<head>
<meta charset="utf-8">
<title>Halloran Field Services – Business Card</title>
<link rel="stylesheet" href="https://fonts.googleapis.com/css2?family=Roboto:wght@400;700&family=Exo+2:wght@600&display=swap">
<style>
  :root {
    --backdrop: #d6d6d6;
    --card-grey: #555557;
    --card-white: #ffffff;
    --accent-orange: #f7941d;
    --ink-dark: #58585a;
    --ink-light: #ffffff;
    --emboss-light: #c9c9cb;
    --emboss-mark: #4a4a4c;
  }
  * { margin: 0; padding: 0; box-sizing: border-box; }
  html, body {
    width: 1200px; height: 801px; overflow: hidden;
    background: var(--backdrop);
    font-family: "Roboto", Arial, sans-serif;
  }
  .card {
    position: absolute; top: 274px;
    width: 443px; height: 263px;
    background: var(--card-grey);
    overflow: hidden;
  }
  .card--services { left: 153px; }
  .card--brand { left: 625px; }

  .card__divider { position: absolute; inset: 0; }

  .brand-block {
    position: absolute; left: 14px; top: 28px; width: 174px;
    text-align: center;
  }
  .brand-block__mark {
    width: 80px; height: 80px; border-radius: 50%;
    background: var(--ink-dark); margin: 0 auto 8px;
  }
  .brand-block__name {
    font-weight: 700; font-size: 17px; line-height: 1.15;
    color: var(--ink-dark);
  }

  .contact {
    position: absolute; right: 29px; top: 50px;
    text-align: right; color: var(--ink-light);
  }
  .contact__name { font-weight: 700; font-size: 18px; line-height: 22px; }
  .contact__phone { font-weight: 400; font-size: 18px; line-height: 22px; }

  .services {
    position: absolute; right: 12px; top: 108px;
    list-style: none; text-align: right; color: var(--ink-light);
    font-size: 12.3px; line-height: 14.6px;
  }
  .services__item {
    display: flex; justify-content: flex-end; align-items: flex-start;
    margin-bottom: 5px;
  }
  .services__item::after {
    content: ""; flex: none;
    width: 8px; height: 8px; border-radius: 50%;
    background: var(--accent-orange);
    margin: 4px 0 0 6px;
  }

  .emboss {
    position: absolute; left: 0; right: 0; top: 44px;
    text-align: center;
  }
  .emboss__mark {
    width: 112px; height: 112px; border-radius: 50%;
    background: var(--emboss-mark); margin: 0 auto 14px;
  }
  .emboss__name {
    font-weight: 700; font-size: 22px; color: var(--emboss-light);
    letter-spacing: 0.3px;
  }
  .emboss__tagline {
    font-family: "Exo 2", Arial, sans-serif; font-weight: 600;
    font-size: 17.5px; color: var(--emboss-light);
    margin-top: 8px; letter-spacing: 0.4px;
  }
</style>
</head>
<body>
  <section class="card card--services">
    <svg class="card__divider" width="443" height="263" viewBox="0 0 443 263">
      <path d="M0,0 H240 C250,90 200,200 99,263 H0 Z" fill="var(--card-white)"/>
      <path d="M239,0 H251 C262,105 205,210 99,263 C190,198 248,95 239,0 Z" fill="var(--accent-orange)"/>
    </svg>
    <div class="brand-block">
      <div class="brand-block__mark"></div>
      <p class="brand-block__name">Halloran Field Services</p>
    </div>
    <div class="contact">
      <p class="contact__name">Contact GUS</p>
      <p class="contact__phone">0417 552 308</p>
    </div>
    <ul class="services">
      <li class="services__item">Bulk fertilizer including Lime<br>Gypsum, Manure &amp; Compost</li>
      <li class="services__item">Granular fertilizer including<br>Single Super, Urea, Gran-am<br>Custom Blends</li>
      <li class="services__item">Modern equipment</li>
      <li class="services__item">Autosteer &amp; Variable Rate Capable</li>
      <li class="services__item">Friendly &amp; Reliable Service</li>
    </ul>
  </section>

  <section class="card card--brand">
    <div class="emboss">
      <div class="emboss__mark"></div>
      <p class="emboss__name">Halloran Field Services</p>
      <p class="emboss__tagline">CUSTOMISED SPREADING</p>
    </div>
  </section>
</body>
</html>
```